Website Home Page for Women's Health Medical Office

Redesign existing homepage for website using existing logo. Current website location is www.meadowcrestwomens.com. Please give it a modern, streamlined, playful feel.

Please give it a feminine feel and make it bright and cheerful using logo colors.

Target Market(s)

Women between the ages of 25-45

Industry/Entity Type

Medical Office

Coding

Coded - Design and coding required

Number of Pages Required

1 page

Font styles to use
Sans Serif
Other font styles liked:
• SEGOI UI script for text and GIL SANS for bold (or their equivilent)

Colors
E54698
E96AAD
F1A4CE
F9D9EA
FCEFF6

Requirements
Must have
• Existing logo. Logo Colors. Feminine, cheerful, simple design. all relevant contact information
Nice to have
• clean lines and streamlined look
Should not have
• Cluttered

```html
<!DOCTYPE html>
<html lang="en">
<head>
<meta charset="utf-8">
<title>Meadowcrest OB/GYN – Home Page Concepts</title>
<link href="https://fonts.googleapis.com/css2?family=Open+Sans:wght@400;600&family=Ubuntu:wght@500;700&display=swap" rel="stylesheet">
<style>
:root{
  --pink:#ec1b8d;
  --pink-mid:#f06aae;
  --pink-soft:#f6b9d8;
  --blush:#fbe3ef;
  --mist:#fcf1f7;
  --backdrop:#f5c4dc;
  --ink:#1f1f24;
  --grey:#55555c;
  --white:#ffffff;
}
*{box-sizing:border-box;margin:0;padding:0}
html,body{width:755px;height:1200px;overflow:hidden;background:var(--backdrop)}
body{font-family:"Open Sans",sans-serif;color:var(--ink)}
.stage{position:absolute;left:0;top:0;width:1510px;height:2400px;transform:scale(.5);transform-origin:0 0}
.page{position:absolute;top:45px;width:695px;background:var(--white);overflow:hidden}
.page--a{left:50px;height:2318px}
.page--b{left:770px;height:2295px}
.abs{position:absolute}
ul{list-style:none}

/* header */
.brand{position:absolute;left:62px;top:0;width:112px;height:88px;background:var(--white);border-radius:0 0 44px 44px;z-index:5;display:flex;align-items:center;justify-content:center;gap:5px;padding-top:8px}
.brand-dot{width:12px;height:12px;border-radius:50%;background:var(--pink);flex:none}
.brand-name{font-family:"Ubuntu",sans-serif;font-weight:700;font-size:11px;line-height:13px;color:var(--pink)}
.contact-item{position:absolute;top:18px;display:flex;gap:8px;align-items:flex-start}
.contact-icon{width:28px;height:28px;border-radius:50%;background:var(--blush);border:1.5px solid var(--pink-soft);display:flex;align-items:center;justify-content:center;flex:none}
.contact-label{font-size:8.5px;color:var(--pink);font-weight:600;line-height:11px}
.contact-text{font-size:7.5px;color:var(--grey);line-height:10px}
.main-nav{position:absolute;left:212px;top:55px;width:483px;height:26px;background:var(--pink);clip-path:polygon(12px 0,100% 0,100% 100%,0 100%);z-index:4}
.main-nav a{position:absolute;top:6px;font-size:9.5px;color:var(--white);text-decoration:none}

/* hero photo area: soft tonal fill */
.hero-photo{position:absolute;left:0;top:75px;width:695px;height:450px;
  background:
    radial-gradient(ellipse 90px 80px at 300px 95px,rgba(222,178,150,.75),rgba(222,178,150,0) 100%),
    radial-gradient(ellipse 75px 70px at 70px 170px,rgba(226,186,160,.7),rgba(226,186,160,0) 100%),
    radial-gradient(ellipse 110px 130px at 300px 250px,rgba(255,255,255,.95),rgba(255,255,255,0) 100%),
    radial-gradient(ellipse 150px 110px at 140px 330px,rgba(250,250,252,.95),rgba(250,250,252,0) 100%),
    radial-gradient(ellipse 110px 70px at 250px 360px,rgba(232,190,165,.7),rgba(232,190,165,0) 100%),
    radial-gradient(ellipse 130px 50px at 330px 430px,rgba(120,150,195,.55),rgba(120,150,195,0) 100%),
    radial-gradient(ellipse 60px 50px at 310px 40px,rgba(110,70,45,.45),rgba(110,70,45,0) 100%),
    linear-gradient(100deg,#ece6ec 0%,#f3eef3 40%,#ebe5ec 70%,#f1edf2 100%)}
.hero-copy{position:absolute;right:65px;top:200px;text-align:right;z-index:3}
.eyebrow{font-family:"Ubuntu",sans-serif;font-weight:500;font-size:13px;color:var(--ink);display:inline-block;padding-bottom:3px;border-bottom:2px solid var(--ink)}
.hero-title{font-family:"Ubuntu",sans-serif;font-weight:500;font-size:24px;line-height:30px;color:var(--pink);margin-top:12px;letter-spacing:.5px}
.hero-text{font-size:8.7px;line-height:12.5px;color:var(--grey);width:200px;margin:9px 0 0 auto}
.btn{display:inline-block;background:var(--pink);color:var(--white);font-size:8.5px;font-weight:600;padding:7px 11px;border-radius:0 10px 0 10px}
.hero-copy .btn{margin-top:9px}

/* section heads */
.section-head{position:absolute;left:0;width:695px;text-align:center}
.section-kicker{font-family:"Ubuntu",sans-serif;font-weight:500;font-size:10.5px;color:var(--ink)}
.section-title{font-family:"Ubuntu",sans-serif;font-weight:500;font-size:17px;color:var(--pink);margin-top:9px;position:relative}
.section-title::before{content:"";position:absolute;left:50%;top:-6px;width:34px;height:1.5px;background:var(--pink);transform:translateX(-50%)}
.section-text{font-size:8.3px;line-height:12.5px;color:var(--grey);width:550px;margin:6px auto 0}

/* services */
.service-card{position:absolute;top:632px;width:132px;text-align:center}
.service-photo{width:132px;height:101px;border-radius:3px}
.photo-care{background:radial-gradient(ellipse 30px 40px at 35px 60px,#f4f4f6,rgba(244,244,246,0) 100%),radial-gradient(ellipse 35px 45px at 95px 65px,#c7cfe4,rgba(199,207,228,0) 100%),radial-gradient(ellipse 25px 30px at 120px 70px,#b9786a,rgba(185,120,106,0) 100%),linear-gradient(180deg,#b98d72,#e8ddd6 45%,#d9cfca)}
.photo-birth{background:radial-gradient(ellipse 55px 40px at 55px 50px,#f3c2bc,rgba(243,194,188,0) 100%),radial-gradient(ellipse 40px 50px at 120px 40px,#f0d7cf,rgba(240,215,207,0) 100%),linear-gradient(160deg,#e9d3cc 0%,#e6b2ab 55%,#49b8d8 100%)}
.photo-exam{background:radial-gradient(ellipse 40px 30px at 60px 70px,#f7f7f8,rgba(247,247,248,0) 100%),radial-gradient(ellipse 25px 55px at 118px 45px,#283448,rgba(40,52,72,0) 100%),linear-gradient(160deg,#6f86a6 0%,#c9d3df 40%,#eef0f3 100%)}
.photo-health{background:radial-gradient(ellipse 30px 35px at 66px 55px,#7c95c9,rgba(124,149,201,0) 100%),radial-gradient(ellipse 60px 18px at 66px 92px,#a88bb4,rgba(168,139,180,0) 100%),linear-gradient(180deg,#f1f0f2 0%,#e4e3e7 70%,#cdbfd4 100%)}
.service-name{font-family:"Ubuntu",sans-serif;font-weight:500;font-size:11px;color:var(--pink);margin-top:7px}
.service-text{font-size:6.8px;line-height:10px;color:var(--grey);margin-top:3px;padding:0 6px;height:32px}
.service-card .btn{font-size:6.5px;padding:5px 10px;margin-top:5px}

/* about */
.about-band{position:absolute;left:0;width:695px;background:linear-gradient(180deg,var(--blush),var(--mist))}
.split-copy{position:absolute;width:278px}
.split-copy .section-kicker{display:inline-block;border-bottom:1.5px solid var(--ink);padding-bottom:2px;font-size:12px}
.split-title{font-family:"Ubuntu",sans-serif;font-weight:500;font-size:17px;line-height:22px;color:var(--pink);margin-top:10px}
.split-text{font-size:8.5px;line-height:12.9px;color:var(--grey);text-align:justify;margin-top:5px}
.split-copy .btn{margin-top:9px;font-size:8.5px;padding:8px 11px}

/* resources */
.resource{position:absolute;top:1465px;width:170px;text-align:center}
.resource-icon{width:64px;height:64px;border-radius:50%;background:var(--blush);margin:0 auto;display:flex;align-items:center;justify-content:center}
.resource-name{font-family:"Ubuntu",sans-serif;font-weight:500;font-size:12px;color:var(--pink);margin-top:14px}
.resource-text{font-size:8.2px;line-height:12.5px;color:var(--grey);margin-top:6px;padding:0 14px}
.resource .btn{margin-top:9px;font-size:8px;padding:7px 11px}
.divider{position:absolute;top:1480px;width:1px;height:130px;background:#e2d7dd}

/* specialists */
.spec-band{position:absolute;left:0;top:1698px;width:695px;height:420px;background:linear-gradient(180deg,#f6eef3,var(--blush))}

/* footer */
.footer{position:absolute;left:0;width:695px;height:200px}
.footer-brand{position:absolute;left:40px;top:0;width:120px;height:95px;display:flex;align-items:center;gap:5px}
.socials{position:absolute;left:44px;top:105px;display:flex;gap:7px}
.socials span{width:16px;height:16px;border-radius:50%;background:var(--pink)}
.foot-col{position:absolute;top:6px}
.foot-title{font-family:"Ubuntu",sans-serif;font-weight:500;font-size:9.5px;color:var(--pink);letter-spacing:.3px}
.foot-list li{font-size:8.3px;color:var(--ink);margin-top:9px;padding-left:3px}
.foot-contact{font-size:7.8px;line-height:10.5px;color:var(--ink);margin-top:9px;padding-left:15px;position:relative}
.foot-contact b{display:block;color:var(--pink);font-weight:600;font-size:7px}
.foot-contact svg{position:absolute;left:0;top:3px}
.subscribe-note{font-size:8px;color:var(--ink);margin-top:9px}
.subscribe-field{margin-top:9px;width:158px;height:22px;border-radius:11px;background:#ececec;position:relative;font-size:6.5px;color:#888;padding:7px 0 0 9px}
.subscribe-field span{position:absolute;right:0;top:0;height:22px;width:50px;border-radius:11px;background:var(--pink);color:var(--white);font-weight:600;font-size:6.5px;text-align:center;line-height:22px}
.footer-rule{position:absolute;left:40px;top:158px;width:590px;height:1px;background:#ddd}
.copyright{position:absolute;left:0;top:170px;width:695px;text-align:center;font-size:8.3px;color:var(--ink)}

/* variant offsets */
.page--a .about-copy{left:65px;top:1005px}
.page--b .about-copy{left:65px;top:985px}
.page--a .footer{top:2130px}
.page--b .footer{top:2107px}
</style>
</head>
<body>
<svg width="0" height="0" style="position:absolute" aria-hidden="true">
  <defs>
    <linearGradient id="ribbon" x1="0" x2="1"><stop offset="0" stop-color="#f06aae"/><stop offset="1" stop-color="#ec1b8d"/></linearGradient>
    <radialGradient id="portraitTone" cx="0.5" cy="0.35" r="0.75">
      <stop offset="0" stop-color="#c99883"/>
      <stop offset="0.22" stop-color="#8a6a5c"/>
      <stop offset="0.45" stop-color="#4d5466"/>
      <stop offset="1" stop-color="#2c3245"/>
    </radialGradient>
    <linearGradient id="scrubsTone" x1="0" y1="0" x2="0" y2="1"><stop offset="0" stop-color="#2a3350" stop-opacity="0"/><stop offset="1" stop-color="#1e2747"/></linearGradient>
    <radialGradient id="nurseTone" cx="0.38" cy="0.3" r="0.8">
      <stop offset="0" stop-color="#d9a88c"/>
      <stop offset="0.25" stop-color="#b3c6d9"/>
      <stop offset="0.6" stop-color="#8eafcc"/>
      <stop offset="1" stop-color="#6f93b6"/>
    </radialGradient>
    <radialGradient id="babyTone" cx="0.45" cy="0.5" r="0.7">
      <stop offset="0" stop-color="#f0c8ba"/>
      <stop offset="0.6" stop-color="#dcae9e"/>
      <stop offset="1" stop-color="#b99a8c"/>
    </radialGradient>
  </defs>
</svg>
<div class="stage">

<!-- ============ Concept A ============ -->
<section class="page page--a">
  <div class="hero-photo" role="img" aria-label="Photo of a smiling doctor gently examining a pregnant patient"></div>
  <svg class="abs" style="left:0;top:360px" width="695" height="180" viewBox="0 0 695 180">
    <path d="M0,115 C40,150 120,170 190,165 C330,150 470,70 695,110 L695,180 L0,180Z" fill="#fff"/>
    <path d="M150,165 C320,120 480,60 695,95 L695,135 C520,95 360,120 150,165Z" fill="url(#ribbon)"/>
    <path d="M330,150 C470,110 580,110 695,130 L695,150 C580,125 470,125 330,150Z" fill="#f6b9d8"/>
  </svg>

  <div class="brand"><span class="brand-dot"></span><span class="brand-name">Meadowcrest<br>OB/GYN</span></div>
  <div class="contact-item" style="left:215px">
    <span class="contact-icon"><svg width="10" height="12" viewBox="0 0 10 12"><path d="M5 0C2.2 0 0 2.2 0 4.8 0 8.4 5 12 5 12s5-3.6 5-7.2C10 2.2 7.8 0 5 0z" fill="#ec1b8d"/><circle cx="5" cy="4.8" r="1.8" fill="#fff"/></svg></span>
    <div><div class="contact-label">Location :</div><div class="contact-text">1840 Willow Bend Road, Suite<br>120, Fairview, CA 90210</div></div>
  </div>
  <div class="contact-item" style="left:382px">
    <span class="contact-icon"><svg width="12" height="9" viewBox="0 0 12 9"><rect width="12" height="9" rx="1" fill="#ec1b8d"/><path d="M0.5 1 6 5 11.5 1" stroke="#fff" fill="none"/></svg></span>
    <div><div class="contact-label">Email Us :</div><div class="contact-text">admin@meadowcrestwomens.com</div></div>
  </div>
  <div class="contact-item" style="left:528px">
    <span class="contact-icon"><svg width="11" height="11" viewBox="0 0 11 11"><path d="M2.2 0.5 4 3 3 4.3C3.7 5.8 5.2 7.3 6.7 8L8 7 10.5 8.8 9.6 10.5C5 10.3 0.7 6 0.5 1.4Z" fill="#ec1b8d"/></svg></span>
    <div><div class="contact-label">Phone Us :</div><div class="contact-text" style="font-size:8.5px">(555) 014-2390</div></div>
  </div>
  <nav class="main-nav"><a style="left:28px">Home</a><a style="left:88px">Services</a><a style="left:158px">Resources</a><a style="left:238px">About Us</a><a style="left:310px">Contact Us</a></nav>

  <div class="hero-copy">
    <div class="eyebrow">WELCOME TO</div>
    <h1 class="hero-title">MEADOWCREST OB/GYN,<br>FAIRVIEW, CA</h1>
    <p class="hero-text">At Meadowcrest OB/GYN in Fairview, California, we believe better health starts when the patient is educated.</p>
    <span class="btn">Learn More</span>
  </div>

  <div class="section-head" style="top:540px">
    <div class="section-kicker">HOW CAN WE HELP YOU?</div>
    <h2 class="section-title">HEALTH SERVICES OFFERED</h2>
    <p class="section-text">Lorem ipsum dolor sit amet, consectetur adipiscing elit, sed do eiusmod tempor incididunt ut labore et dolore magna aliqua. Ut enim ad minim veniam, quis nostrud exercitation ullamco laboris nisi ut aliquip ex ea commodo consequat.</p>
  </div>
  <div class="service-card" style="left:63px"><div class="service-photo photo-care" role="img" aria-label="Photo of a doctor checking a pregnant patient"></div><div class="service-name">Pregnancy Care</div><p class="service-text">Receiving regular care in pregnancy is important for the health of both you and your baby.</p><span class="btn">Read More</span></div>
  <div class="service-card" style="left:208px"><div class="service-photo photo-birth" role="img" aria-label="Photo of a newborn resting on its mother"></div><div class="service-name">Birth Control</div><p class="service-text">Our gynecologists are knowledgeable on all forms of birth control including</p><span class="btn">Read More</span></div>
  <div class="service-card" style="left:352px"><div class="service-photo photo-exam" role="img" aria-label="Photo of a doctor writing notes at a desk"></div><div class="service-name">Well Woman Exams</div><p class="service-text">Our providers will help you to stay healthy by performing a physical exam on you annually.</p><span class="btn">Read More</span></div>
  <div class="service-card" style="left:497px"><div class="service-photo photo-health" role="img" aria-label="Photo of a woman meditating at home"></div><div class="service-name">Women's Health</div><p class="service-text">Whether you are dealing with painful or irregular periods, fibroids, or other women's health i ssues</p><span class="btn">Read More</span></div>

  <div class="about-band" style="top:900px;height:460px"></div>
  <svg class="abs" style="left:0;top:850px" width="695" height="130" viewBox="0 0 695 130">
    <path d="M0,0 L695,0 L695,60 C560,55 420,70 300,100 C200,125 80,120 0,95Z" fill="#fff"/>
    <path d="M0,40 C60,80 150,110 250,100 C400,80 520,40 695,45 L695,55 C520,55 400,95 250,115 C150,125 60,100 0,75Z" fill="url(#ribbon)"/>
    <path d="M0,60 C80,95 170,105 250,100 L250,105 C170,115 80,110 0,80Z" fill="#f6b9d8"/>
  </svg>
  <div class="split-copy about-copy">
    <div class="section-kicker">ABOUT TO</div>
    <h2 class="split-title">SERVING WILLOW SPRINGS<br>MEDICAL CENTER</h2>
    <p class="split-text">At Meadowcrest OB/GYN in Fairview, California, we believe better health starts when the patient is educated. For this reason, we take time to listen to our patients concerns, explain each option available, and to answer any questions our patients may have so that they can make informed decisions. At Meadowcrest OB/GYN, our providers tailor every procedure performed and treatment option recommended to meet the specific needs of our patients. We remain up-to-date on the latest technology and practice guidelines for women's health.</p>
    <span class="btn">Learn More</span>
  </div>
  <svg class="abs" style="left:365px;top:990px" width="270" height="240" viewBox="0 0 270 240" role="img" aria-label="Portrait photo of a smiling physician in navy scrubs">
    <path d="M60,40 C100,0 190,0 235,40 C270,75 270,140 240,180 C200,235 110,240 55,215 C10,195 0,140 20,95 C30,70 40,55 60,40Z" fill="#ec1b8d"/>
    <path d="M75,55 C115,15 200,20 230,70 C255,115 235,180 190,205 C140,230 80,220 55,185 C30,150 40,95 75,55Z" fill="url(#portraitTone)"/>
    <path d="M55,185 C70,160 110,150 140,150 C175,150 210,160 225,150 C230,175 215,195 190,205 C140,230 80,220 55,185Z" fill="url(#scrubsTone)"/>
  </svg>
  <svg class="abs" style="left:0;top:1280px" width="695" height="110" viewBox="0 0 695 110">
    <path d="M0,60 C150,110 330,100 480,70 C560,55 630,50 695,55 L695,110 L0,110Z" fill="#fff"/>
    <path d="M200,95 C360,70 500,20 695,55 L695,80 C520,50 380,90 200,95Z" fill="url(#ribbon)"/>
  </svg>

  <div class="section-head" style="top:1365px">
    <div class="section-kicker">WHAT WE DO</div>
    <h2 class="section-title">RESOURCES</h2>
    <p class="section-text">Lorem ipsum dolor sit amet, consectetur adipiscing elit, sed do eiusmod tempor incididunt ut labore et dolore magna aliqua. Ut enim ad minim veniam, quis nostrud exercitation ullamco laboris nisi ut aliquip ex ea commodo consequat.</p>
  </div>
  <div class="resource" style="left:72px"><div class="resource-icon"><svg width="36" height="28" viewBox="0 0 36 28"><circle cx="18" cy="6" r="5" fill="#ec1b8d"/><circle cx="7" cy="9" r="4" fill="#ec1b8d"/><circle cx="29" cy="9" r="4" fill="#ec1b8d"/><path d="M10,28 C10,16 26,16 26,28Z M0,28 C0,18 10,16 12,20 L9,28Z M36,28 C36,18 26,16 24,20 L27,28Z" fill="#ec1b8d"/></svg></div><div class="resource-name">Downloads</div><p class="resource-text">Lorem ipsum dolor sit amet, consectetur adipiscing elit, sed do eiusmod tempor et dolore magna aliqua.</p><span class="btn">Learn More</span></div>
  <div class="divider" style="left:255px"></div>
  <div class="resource" style="left:272px"><div class="resource-icon"><svg width="34" height="30" viewBox="0 0 34 30"><rect x="1" y="1" width="32" height="21" rx="2" fill="#ec1b8d"/><circle cx="17" cy="11" r="6" fill="none" stroke="#fff" stroke-width="1.5"/><path d="M11,11 H23 M17,5 V17" stroke="#fff" stroke-width="1.2"/><rect x="13" y="22" width="8" height="5" fill="#ec1b8d"/><rect x="9" y="27" width="16" height="2.5" fill="#ec1b8d"/></svg></div><div class="resource-name">Patient Portal</div><p class="resource-text">Lorem ipsum dolor sit amet, consectetur adipiscing elit, sed do eiusmod tempor et dolore magna aliqua.</p><span class="btn">Learn More</span></div>
  <div class="divider" style="left:457px"></div>
  <div class="resource" style="left:473px"><div class="resource-icon"><svg width="26" height="32" viewBox="0 0 26 32"><path d="M0,2 Q0,0 2,0 H18 L26,8 V30 Q26,32 24,32 H2 Q0,32 0,30Z" fill="#ec1b8d"/><path d="M7,14 H19 M7,19 H19 M7,24 H19" stroke="#fff" stroke-width="1.6"/></svg></div><div class="resource-name">Patient Forms</div><p class="resource-text">Lorem ipsum dolor sit amet, consectetur adipiscing elit, sed do eiusmod tempor et dolore magna aliqua.</p><span class="btn">Learn More</span></div>

  <div class="spec-band"></div>
  <svg class="abs" style="left:65px;top:1683px" width="285" height="290" viewBox="0 0 285 290" role="img" aria-label="Photo of a nurse holding a newborn baby">
    <path d="M40,95 C70,60 120,70 150,60 C200,45 240,60 245,110 C250,160 280,200 240,250 C200,290 110,290 60,260 C10,230 0,150 40,95Z" fill="#ec1b8d"/>
    <path d="M55,105 C80,10 200,0 225,70 C235,100 280,120 275,170 L275,265 L150,265 C90,270 20,230 25,170 C28,140 45,125 55,105Z" fill="url(#nurseTone)"/>
    <rect x="170" y="135" width="105" height="130" fill="url(#babyTone)"/>
  </svg>
  <div class="split-copy" style="left:362px;top:1748px;width:276px">
    <div class="section-kicker">SPECIALISTS</div>
    <h2 class="split-title">YOUR OB/GYN<br>SPECIALISTS</h2>
    <p class="split-text">Meadowcrest OB/GYN offers you the best care possible in a personalized setting. We are currently accepting patients. Call our office now to make an appointment.</p>
    <p class="split-text">Meadowcrest OB/GYN (located near Willow Springs Hospital in Fairview, CA) is a medical office that specializes in Christ-centered healthcare for women of all ages. Our team of exclusively female providers have years of experience taking care of women with a variety of pregnancy and gynecology concerns.</p>
    <span class="btn">Learn More</span>
  </div>
  <svg class="abs" style="left:0;top:1990px" width="695" height="130" viewBox="0 0 695 130">
    <path d="M0,70 C60,110 140,120 230,100 C380,70 520,50 695,60 L695,130 L0,130Z" fill="#fff"/>
    <path d="M0,40 C70,95 150,110 250,90 C400,60 540,40 695,55 L695,65 C540,55 400,85 250,112 C150,130 60,110 0,80Z" fill="url(#ribbon)"/>
  </svg>

  <footer class="footer">
    <div class="footer-brand"><span class="brand-dot"></span><span class="brand-name" style="font-size:12px;line-height:14px">Meadowcrest<br>OB/GYN</span></div>
    <div class="socials"><span></span><span></span><span></span><span></span></div>
    <div class="foot-col" style="left:178px"><div class="foot-title">QUICK LINKS</div><ul class="foot-list"><li>Home</li><li>Services</li><li>Resources</li><li>About Us</li><li>Contact Us</li></ul></div>
    <div class="foot-col" style="left:267px"><div class="foot-title">HELP LINKS</div><ul class="foot-list"><li>Copyright</li><li>Legal</li><li>Privacy</li><li>Accessibility</li><li>Sitemap</li></ul></div>
    <div class="foot-col" style="left:353px;width:135px"><div class="foot-title">CONTACT US</div>
      <div class="foot-contact"><svg width="8" height="10" viewBox="0 0 10 12"><path d="M5 0C2.2 0 0 2.2 0 4.8 0 8.4 5 12 5 12s5-3.6 5-7.2C10 2.2 7.8 0 5 0z" fill="#ec1b8d"/></svg><b>Address</b>1840 Willow Bend Road, Suite 120, Fairview, Ca 90210</div>
      <div class="foot-contact"><svg width="9" height="9" viewBox="0 0 11 11"><path d="M2.2 0.5 4 3 3 4.3C3.7 5.8 5.2 7.3 6.7 8L8 7 10.5 8.8 9.6 10.5C5 10.3 0.7 6 0.5 1.4Z" fill="#ec1b8d"/></svg><b>Call Us</b>(555) 014-2390</div>
      <div class="foot-contact"><svg width="9" height="7" viewBox="0 0 12 9"><rect width="12" height="9" fill="#ec1b8d"/></svg><b>Email</b>admin@meadowcrestwomens.com</div>
    </div>
    <div class="foot-col" style="left:493px;top:0"><div class="foot-title">SUBSCRIBE FOR UPDATES</div><div class="subscribe-note">Now Accepting New Patients</div><div class="subscribe-field">Email Address<span>SIGN UP</span></div></div>
    <div class="footer-rule"></div>
    <div class="copyright">©2022. ALL RIGHTS RESERVED.</div>
  </footer>
</section>

<!-- ============ Concept B ============ -->
<section class="page page--b">
  <div class="hero-photo" role="img" aria-label="Photo of a smiling doctor gently examining a pregnant patient"></div>
  <svg class="abs" style="left:0;top:340px" width="695" height="200" viewBox="0 0 695 200">
    <path d="M0,170 C120,110 260,120 400,125 C560,130 650,80 695,10 L695,200 L0,200Z" fill="#fff"/>
    <path d="M0,170 C120,110 260,120 400,125 C560,130 650,80 695,10" fill="none" stroke="#ec1b8d" stroke-width="3"/>
    <path d="M0,178 C120,122 260,130 400,133 C560,138 655,90 695,25" fill="none" stroke="#ec1b8d" stroke-width="2"/>
    <path d="M20,180 C140,130 270,138 400,141 C560,146 660,100 695,40" fill="none" stroke="#f06aae" stroke-width="1.5"/>
  </svg>

  <div class="brand"><span class="brand-dot"></span><span class="brand-name">Meadowcrest<br>OB/GYN</span></div>
  <div class="contact-item" style="left:215px">
    <span class="contact-icon"><svg width="10" height="12" viewBox="0 0 10 12"><path d="M5 0C2.2 0 0 2.2 0 4.8 0 8.4 5 12 5 12s5-3.6 5-7.2C10 2.2 7.8 0 5 0z" fill="#ec1b8d"/><circle cx="5" cy="4.8" r="1.8" fill="#fff"/></svg></span>
    <div><div class="contact-label">Location :</div><div class="contact-text">1840 Willow Bend Road, Suite<br>120, Fairview, CA 90210</div></div>
  </div>
  <div class="contact-item" style="left:382px">
    <span class="contact-icon"><svg width="12" height="9" viewBox="0 0 12 9"><rect width="12" height="9" rx="1" fill="#ec1b8d"/><path d="M0.5 1 6 5 11.5 1" stroke="#fff" fill="none"/></svg></span>
    <div><div class="contact-label">Email Us :</div><div class="contact-text">admin@meadowcrestwomens.com</div></div>
  </div>
  <div class="contact-item" style="left:528px">
    <span class="contact-icon"><svg width="11" height="11" viewBox="0 0 11 11"><path d="M2.2 0.5 4 3 3 4.3C3.7 5.8 5.2 7.3 6.7 8L8 7 10.5 8.8 9.6 10.5C5 10.3 0.7 6 0.5 1.4Z" fill="#ec1b8d"/></svg></span>
    <div><div class="contact-label">Phone Us :</div><div class="contact-text" style="font-size:8.5px">(555) 014-2390</div></div>
  </div>
  <nav class="main-nav"><a style="left:28px">Home</a><a style="left:88px">Services</a><a style="left:158px">Resources</a><a style="left:238px">About Us</a><a style="left:310px">Contact Us</a></nav>

  <div class="hero-copy">
    <div class="eyebrow">WELCOME TO</div>
    <h1 class="hero-title">MEADOWCREST OB/GYN,<br>FAIRVIEW, CA</h1>
    <p class="hero-text">At Meadowcrest OB/GYN in Fairview, California, we believe better health starts when the patient is educated.</p>
    <span class="btn">Learn More</span>
  </div>

  <div class="section-head" style="top:540px">
    <div class="section-kicker">HOW CAN WE HELP YOU?</div>
    <h2 class="section-title">HEALTH SERVICES OFFERED</h2>
    <p class="section-text">Lorem ipsum dolor sit amet, consectetur adipiscing elit, sed do eiusmod tempor incididunt ut labore et dolore magna aliqua. Ut enim ad minim veniam, quis nostrud exercitation ullamco laboris nisi ut aliquip ex ea commodo consequat.</p>
  </div>
  <div class="service-card" style="left:63px"><div class="service-photo photo-care" role="img" aria-label="Photo of a doctor checking a pregnant patient"></div><div class="service-name">Pregnancy Care</div><p class="service-text">Receiving regular care in pregnancy is important for the health of both you and your baby.</p><span class="btn">Read More</span></div>
  <div class="service-card" style="left:208px"><div class="service-photo photo-birth" role="img" aria-label="Photo of a newborn resting on its mother"></div><div class="service-name">Birth Control</div><p class="service-text">Our gynecologists are knowledgeable on all forms of birth control including</p><span class="btn">Read More</span></div>
  <div class="service-card" style="left:352px"><div class="service-photo photo-exam" role="img" aria-label="Photo of a doctor writing notes at a desk"></div><div class="service-name">Well Woman Exams</div><p class="service-text">Our providers will help you to stay healthy by performing a physical exam on you annually.</p><span class="btn">Read More</span></div>
  <div class="service-card" style="left:497px"><div class="service-photo photo-health" role="img" aria-label="Photo of a woman meditating at home"></div><div class="service-name">Women's Health</div><p class="service-text">Whether you are dealing with painful or irregular periods, fibroids, or other women's health i ssues</p><span class="btn">Read More</span></div>

  <div class="about-band" style="top:880px;height:415px"></div>
  <svg class="abs" style="left:0;top:860px" width="695" height="110" viewBox="0 0 695 110">
    <path d="M0,0 L695,0 L695,10 C600,60 520,95 420,95 C320,95 200,50 110,55 C50,60 15,85 0,110Z" fill="#fff"/>
    <path d="M0,110 C15,85 50,60 110,55 C200,50 320,95 420,95 C520,95 600,60 695,10" fill="none" stroke="#ec1b8d" stroke-width="3"/>
  </svg>
  <div class="split-copy about-copy">
    <div class="section-kicker">ABOUT TO</div>
    <h2 class="split-title">SERVING WILLOW SPRINGS<br>MEDICAL CENTER</h2>
    <p class="split-text">At Meadowcrest OB/GYN in Fairview, California, we believe better health starts when the patient is educated. For this reason, we take time to listen to our patients concerns, explain each option available, and to answer any questions our patients may have so that they can make informed decisions. At Meadowcrest OB/GYN, our providers tailor every procedure performed and treatment option recommended to meet the specific needs of our patients. We remain up-to-date on the latest technology and practice guidelines for women's health.</p>
    <span class="btn">Learn More</span>
  </div>
  <svg class="abs" style="left:365px;top:970px" width="270" height="240" viewBox="0 0 270 240" role="img" aria-label="Portrait photo of a smiling physician in navy scrubs">
    <path d="M60,40 C100,0 190,0 235,40 C270,75 270,140 240,180 C200,235 110,240 55,215 C10,195 0,140 20,95 C30,70 40,55 60,40Z" fill="#ec1b8d"/>
    <path d="M75,55 C115,15 200,20 230,70 C255,115 235,180 190,205 C140,230 80,220 55,185 C30,150 40,95 75,55Z" fill="url(#portraitTone)"/>
    <path d="M55,185 C70,160 110,150 140,150 C175,150 210,160 225,150 C230,175 215,195 190,205 C140,230 80,220 55,185Z" fill="url(#scrubsTone)"/>
  </svg>

  <div class="section-head" style="top:1365px">
    <div class="section-kicker">WHAT WE DO</div>
    <h2 class="section-title">RESOURCES</h2>
    <p class="section-text">Lorem ipsum dolor sit amet, consectetur adipiscing elit, sed do eiusmod tempor incididunt ut labore et dolore magna aliqua. Ut enim ad minim veniam, quis nostrud exercitation ullamco laboris nisi ut aliquip ex ea commodo consequat.</p>
  </div>
  <div class="resource" style="left:72px"><div class="resource-icon"><svg width="36" height="28" viewBox="0 0 36 28"><circle cx="18" cy="6" r="5" fill="#ec1b8d"/><circle cx="7" cy="9" r="4" fill="#ec1b8d"/><circle cx="29" cy="9" r="4" fill="#ec1b8d"/><path d="M10,28 C10,16 26,16 26,28Z M0,28 C0,18 10,16 12,20 L9,28Z M36,28 C36,18 26,16 24,20 L27,28Z" fill="#ec1b8d"/></svg></div><div class="resource-name">Downloads</div><p class="resource-text">Lorem ipsum dolor sit amet, consectetur adipiscing elit, sed do eiusmod tempor et dolore magna aliqua.</p><span class="btn">Learn More</span></div>
  <div class="divider" style="left:255px"></div>
  <div class="resource" style="left:272px"><div class="resource-icon"><svg width="34" height="30" viewBox="0 0 34 30"><rect x="1" y="1" width="32" height="21" rx="2" fill="#ec1b8d"/><circle cx="17" cy="11" r="6" fill="none" stroke="#fff" stroke-width="1.5"/><path d="M11,11 H23 M17,5 V17" stroke="#fff" stroke-width="1.2"/><rect x="13" y="22" width="8" height="5" fill="#ec1b8d"/><rect x="9" y="27" width="16" height="2.5" fill="#ec1b8d"/></svg></div><div class="resource-name">Patient Portal</div><p class="resource-text">Lorem ipsum dolor sit amet, consectetur adipiscing elit, sed do eiusmod tempor et dolore magna aliqua.</p><span class="btn">Learn More</span></div>
  <div class="divider" style="left:457px"></div>
  <div class="resource" style="left:473px"><div class="resource-icon"><svg width="26" height="32" viewBox="0 0 26 32"><path d="M0,2 Q0,0 2,0 H18 L26,8 V30 Q26,32 24,32 H2 Q0,32 0,30Z" fill="#ec1b8d"/><path d="M7,14 H19 M7,19 H19 M7,24 H19" stroke="#fff" stroke-width="1.6"/></svg></div><div class="resource-name">Patient Forms</div><p class="resource-text">Lorem ipsum dolor sit amet, consectetur adipiscing elit, sed do eiusmod tempor et dolore magna aliqua.</p><span class="btn">Learn More</span></div>

  <div class="spec-band"></div>
  <svg class="abs" style="left:65px;top:1683px" width="285" height="290" viewBox="0 0 285 290" role="img" aria-label="Photo of a nurse holding a newborn baby">
    <path d="M40,95 C70,60 120,70 150,60 C200,45 240,60 245,110 C250,160 280,200 240,250 C200,290 110,290 60,260 C10,230 0,150 40,95Z" fill="#ec1b8d"/>
    <path d="M55,105 C80,10 200,0 225,70 C235,100 280,120 275,170 L275,265 L150,265 C90,270 20,230 25,170 C28,140 45,125 55,105Z" fill="url(#nurseTone)"/>
    <rect x="170" y="135" width="105" height="130" fill="url(#babyTone)"/>
  </svg>
  <div class="split-copy" style="left:362px;top:1748px;width:276px">
    <div class="section-kicker">SPECIALISTS</div>
    <h2 class="split-title">YOUR OB/GYN<br>SPECIALISTS</h2>
    <p class="split-text">Meadowcrest OB/GYN offers you the best care possible in a personalized setting. We are currently accepting patients. Call our office now to make an appointment.</p>
    <p class="split-text">Meadowcrest OB/GYN (located near Willow Springs Hospital in Fairview, CA) is a medical office that specializes in Christ-centered healthcare for women of all ages. Our team of exclusively female providers have years of experience taking care of women with a variety of pregnancy and gynecology concerns.</p>
    <span class="btn">Learn More</span>
  </div>
  <svg class="abs" style="left:0;top:1940px" width="695" height="180" viewBox="0 0 695 180">
    <path d="M0,170 C80,110 200,110 320,125 C460,145 600,120 695,10 L695,180 L0,180Z" fill="#fff"/>
    <path d="M0,170 C80,110 200,110 320,125 C460,145 600,120 695,10" fill="none" stroke="#ec1b8d" stroke-width="3"/>
    <path d="M10,172 C90,120 205,120 320,133 C460,152 610,128 695,25" fill="none" stroke="#ec1b8d" stroke-width="2"/>
    <path d="M25,174 C100,128 210,128 320,140 C460,158 618,135 695,40" fill="none" stroke="#f06aae" stroke-width="1.5"/>
  </svg>

  <footer class="footer">
    <div class="footer-brand"><span class="brand-dot"></span><span class="brand-name" style="font-size:12px;line-height:14px">Meadowcrest<br>OB/GYN</span></div>
    <div class="socials"><span></span><span></span><span></span><span></span></div>
    <div class="foot-col" style="left:178px"><div class="foot-title">QUICK LINKS</div><ul class="foot-list"><li>Home</li><li>Services</li><li>Resources</li><li>About Us</li><li>Contact Us</li></ul></div>
    <div class="foot-col" style="left:267px"><div class="foot-title">HELP LINKS</div><ul class="foot-list"><li>Copyright</li><li>Legal</li><li>Privacy</li><li>Accessibility</li><li>Sitemap</li></ul></div>
    <div class="foot-col" style="left:353px;width:135px"><div class="foot-title">CONTACT US</div>
      <div class="foot-contact"><svg width="8" height="10" viewBox="0 0 10 12"><path d="M5 0C2.2 0 0 2.2 0 4.8 0 8.4 5 12 5 12s5-3.6 5-7.2C10 2.2 7.8 0 5 0z" fill="#ec1b8d"/></svg><b>Address</b>1840 Willow Bend Road, Suite 120, Fairview, Ca 90210</div>
      <div class="foot-contact"><svg width="9" height="9" viewBox="0 0 11 11"><path d="M2.2 0.5 4 3 3 4.3C3.7 5.8 5.2 7.3 6.7 8L8 7 10.5 8.8 9.6 10.5C5 10.3 0.7 6 0.5 1.4Z" fill="#ec1b8d"/></svg><b>Call Us</b>(555) 014-2390</div>
      <div class="foot-contact"><svg width="9" height="7" viewBox="0 0 12 9"><rect width="12" height="9" fill="#ec1b8d"/></svg><b>Email</b>admin@meadowcrestwomens.com</div>
    </div>
    <div class="foot-col" style="left:493px;top:0"><div class="foot-title">SUBSCRIBE FOR UPDATES</div><div class="subscribe-note">Now Accepting New Patients</div><div class="subscribe-field">Email Address<span>SIGN UP</span></div></div>
    <div class="footer-rule"></div>
    <div class="copyright">©2022. ALL RIGHTS RESERVED.</div>
  </footer>
</section>

</div>
</body>
</html>
```